Modern Verdell Tree Care Website

I need a website for a full service Tree Care company. The company provides tree pruning, tree removal, tree preservation, emergency services, stump grinding, and emergency tree services.

Target Market(s)

Customers that need tree services

Industry/Entity Type

Landscaping, Tree Services

Coding

Coded - Design and coding required

Number of Pages Required

5+ page

Font styles to use
Sans Serif

Requirements
Must have
• Good clean design that showcases the services the company provides.
Nice to have
• Services page; contact form, blog, home page, about page

```html
<!DOCTYPE html>
<html lang="en">
<head>
<meta charset="UTF-8">
<title>Verdell Tree Care</title>
<link href="https://fonts.googleapis.com/css2?family=Audiowide&family=Montserrat:wght@400;500;600;700&display=swap" rel="stylesheet">
<style>
:root{
  --green:#8cc63f;
  --orange:#f7a234;
  --tan:#c9a06c;
  --slate:#4b5560;
  --ink:#1c1c1c;
  --grey-bg:#eeeeee;
  --white:#ffffff;
  --black:#000000;
}
*{margin:0;padding:0;box-sizing:border-box}
html,body{width:1200px;height:3419px;overflow:hidden}
body{position:relative;font-family:'Montserrat',sans-serif;color:var(--ink);background:var(--white)}
.abs{position:absolute}
.display{font-family:'Audiowide',sans-serif;letter-spacing:2px;text-transform:uppercase;font-weight:400}
.top-stripe{left:0;top:0;width:1200px;height:4px;background:linear-gradient(90deg,var(--tan),var(--green),var(--orange))}
.brand{left:110px;top:32px;display:flex;align-items:center;gap:12px}
.brand-dot{width:40px;height:40px;background:var(--green)}
.brand-name{font-weight:700;font-size:24px;color:var(--slate);line-height:1}
.nav{left:440px;top:43px;display:flex;gap:44px;font-size:16px;color:#444}
.pill{display:flex;align-items:center;gap:10px;border-radius:24px;color:var(--white);font-weight:500}
.pill .ring{width:34px;height:34px;border-radius:50%;background:var(--white);display:flex;align-items:center;justify-content:center}
.nav-phone{left:908px;top:32px;width:180px;height:45px;background:var(--green);padding-left:6px;font-size:16px}
.hero{left:0;top:102px;width:1200px;height:760px;background:linear-gradient(135deg,#dfe3d9 0%,#cdd3c5 40%,#a7b19a 70%,#6f7e69 100%)}
.hero-photo{left:688px;top:150px;width:400px;height:400px;background:linear-gradient(160deg,#e4cfa8,#c9d8b0 50%,#7a6a58)}
.hero-title{left:110px;top:280px;font-size:46px;line-height:61px;color:var(--slate)}
.hero-title .o{color:var(--orange)}.hero-title .g{color:var(--green)}
.hero-sub{left:110px;top:482px;font-size:24px;color:var(--ink)}
.hero-phone{left:110px;top:545px;width:178px;height:45px;background:var(--tan);padding-left:5px;font-size:16px}
.section-title{width:1200px;left:0;text-align:center;font-size:31px;color:var(--slate)}
.cta-title{top:1940px;color:var(--white)}
.card{width:308px;height:307px;top:945px;background:var(--white);box-shadow:0 2px 10px rgba(0,0,0,.08);text-align:center}
.card .img{margin:10px 6px 0;height:210px}
.card .badge{width:60px;height:60px;border-radius:50%;background:var(--white);margin:-30px auto 0;position:relative}
.card h3{font-weight:600;font-size:18px;margin-top:8px}
.card a{display:block;color:var(--tan);font-weight:600;font-size:15px;margin-top:10px;text-decoration:none}
.arrow{width:40px;height:40px;border-radius:50%;top:1052px;display:flex;align-items:center;justify-content:center}
.who{left:0;top:1338px;width:1200px;height:514px;background:var(--grey-bg)}
.who-title{left:112px;top:1412px;font-size:30px;color:var(--slate)}
.who-text{left:112px;top:1478px;width:510px;font-size:15px;line-height:24px;color:#333}
.who-text p+p{margin-top:20px}
.btn{background:var(--tan);color:var(--white);font-weight:500;font-size:16px;border-radius:24px;display:flex;align-items:center;justify-content:center}
.cta{left:0;top:1852px;width:1200px;height:386px;background:linear-gradient(100deg,#f7a234 0%,#c7b73d 45%,#8cc63f 100%)}
.field{border:1.5px solid rgba(255,255,255,.8);border-radius:4px;color:var(--white);font-size:12px;padding:13px 16px}
.submit{left:323px;top:2097px;width:553px;height:47px;background:var(--white);border-radius:4px;font-size:12px;font-weight:600;display:flex;align-items:center;justify-content:center;color:#333}
.why-title{left:682px;top:2352px;font-size:30px;color:var(--slate)}
.why-list{left:682px;top:2418px;list-style:none;font-size:20px;color:#333}
.why-list li{display:flex;align-items:center;gap:18px;height:43px}
.footer{left:0;top:2860px;width:1200px;height:559px;background:var(--black)}
.f-text{color:var(--white)}
.f-head{font-weight:600;font-size:18px;color:var(--white)}
.f-head::after{content:"";display:block;width:135px;height:2px;background:var(--orange);margin-top:12px}
.f-links{font-size:14px;line-height:24px;list-style:none;color:var(--white)}
.f-input{left:878px;width:195px;background:var(--white);border-radius:4px;color:#888;font-size:10px;padding:8px 10px}
.social{width:32px;height:32px;border-radius:50%;background:var(--green);border:2px solid var(--white);top:3192px}
</style>
</head>
<body>
<div class="abs top-stripe"></div>
<div class="abs brand"><span class="brand-dot"></span><span class="brand-name">Verdell Tree Care</span></div>
<nav class="abs nav"><span>Home</span><span>Services</span><span>Blog</span><span>About</span><span>Contact</span></nav>
<div class="abs pill nav-phone"><span class="ring"><svg width="18" height="18" viewBox="0 0 24 24" fill="none" stroke="#8cc63f" stroke-width="2"><path d="M5 3h4l2 5-3 2a12 12 0 0 0 6 6l2-3 5 2v4a2 2 0 0 1-2 2A17 17 0 0 1 3 5a2 2 0 0 1 2-2z"/></svg></span>(555) 014-7720</div>

<section class="abs hero" role="img" aria-label="Arborist in safety gear cutting a tree branch with a chainsaw"></section>
<div class="abs hero-photo" role="img" aria-label="Arborist in orange safety shirt and helmet"></div>
<h1 class="abs display hero-title">Call <span class="o">Verdell</span> for<br>all your <span class="g">tree</span><br><span class="g">care</span> needs</h1>
<p class="abs hero-sub">Serving Marrowfield and surrounding areas</p>
<div class="abs pill hero-phone"><span class="ring"><svg width="18" height="18" viewBox="0 0 24 24" fill="none" stroke="#c9a06c" stroke-width="2"><path d="M5 3h4l2 5-3 2a12 12 0 0 0 6 6l2-3 5 2v4a2 2 0 0 1-2 2A17 17 0 0 1 3 5a2 2 0 0 1 2-2z"/></svg></span>(555) 014-7720</div>
<svg class="abs" style="left:0;top:740px" width="1200" height="130" viewBox="0 0 1200 130">
  <path d="M0 100 Q600 0 1100 20 Q1190 30 1200 90 L1200 130 L0 130Z" fill="#fff"/>
  <path d="M0 100 Q600 0 1100 20 Q1190 30 1200 90" fill="none" stroke="#f7a234" stroke-width="6"/>
  <circle cx="600" cy="10" r="30" fill="#fff" stroke="#eee"/>
  <path d="M590 4l10 9 10-9M590 12l10 9 10-9" fill="none" stroke="#666" stroke-width="1.5"/>
</svg>

<h2 class="abs display section-title" style="top:866px">Our Services</h2>
<div class="abs arrow" style="left:48px;background:var(--orange)"><svg width="10" height="10" viewBox="0 0 10 10"><path d="M7 1L3 5l4 4" stroke="#fff" fill="none" stroke-width="1.5"/></svg></div>
<div class="abs arrow" style="left:1112px;border:1.5px solid var(--orange)"><svg width="10" height="10" viewBox="0 0 10 10"><path d="M3 1l4 4-4 4" stroke="#222" fill="none" stroke-width="1.5"/></svg></div>
<div class="abs card" style="left:108px"><div class="img" role="img" aria-label="Pruning shears trimming branches against blue sky" style="background:linear-gradient(160deg,#4a8fd8,#9cc3ea)"></div><div class="badge"></div><h3>Tree Trimming</h3><a>Learn More ›</a></div>
<div class="abs card" style="left:444px"><div class="img" role="img" aria-label="Hands pruning a small branch" style="background:linear-gradient(160deg,#6d7a3a,#b4a47a,#5a5a78)"></div><div class="badge"></div><h3>Tree Pruning</h3><a>Learn More ›</a></div>
<div class="abs card" style="left:780px"><div class="img" role="img" aria-label="Climber removing a tree" style="background:linear-gradient(160deg,#8fb5d8,#6b7a55)"></div><div class="badge"></div><h3>Tree Removal</h3><a>Learn More ›</a></div>

<section class="abs who"></section>
<h2 class="abs display who-title">Who We Are</h2>
<div class="abs who-text"><p>At Verdell tree care we are more than just a tree service company we are stewards of our beautiful trees,with a passion deeply rooted in arboriculture we embark on a mission to promote the health, beauty, and safety of your trees and landscapes.</p><p>Whether it's expert tree trimming to enhance aesthetics, meticulous tree removal to mitigate hazards, or comprehensive tree health assessments to ensure safety, we approach each task with unwavering dedication and attention to detail.</p></div>
<div class="abs btn" style="left:112px;top:1716px;width:132px;height:44px">Learn More</div>
<div class="abs" style="left:738px;top:1390px;width:348px;height:255px;background:linear-gradient(90deg,var(--orange),var(--green))"></div>
<div class="abs" role="img" aria-label="Volunteers planting a young tree by a lake" style="left:694px;top:1406px;width:374px;height:368px;background:linear-gradient(170deg,#8aa0c0,#6f86a8 45%,#cbb894)"></div>

<section class="abs cta" role="img" aria-label="Warm orange to green backdrop"></section>
<h2 class="abs display section-title cta-title">Request A Call Back</h2>
<div class="abs field" style="left:323px;top:2032px;width:270px;height:46px">Name*</div>
<div class="abs field" style="left:606px;top:2032px;width:270px;height:46px">Phone*</div>
<div class="abs submit">SUBMIT NOW</div>

<div class="abs" role="img" aria-label="Chainsaw cutting wood with flying sawdust" style="left:112px;top:2323px;width:492px;height:492px;background:linear-gradient(140deg,#3d3a32,#6b5a40 50%,#c46a2a)"></div>
<h2 class="abs display why-title">Why Choose Us</h2>
<ul class="abs why-list">
  <li><svg width="20" height="20" viewBox="0 0 20 20" fill="none" stroke="#8cc63f" stroke-width="1.8"><circle cx="10" cy="10" r="8"/><path d="M6 10l3 3 5-6"/></svg>Licensed and insured</li>
  <li><svg width="20" height="20" viewBox="0 0 20 20" fill="none" stroke="#8cc63f" stroke-width="1.8"><circle cx="10" cy="10" r="8"/><path d="M6 10l3 3 5-6"/></svg>24-hours emergency services</li>
  <li><svg width="20" height="20" viewBox="0 0 20 20" fill="none" stroke="#8cc63f" stroke-width="1.8"><circle cx="10" cy="10" r="8"/><path d="M6 10l3 3 5-6"/></svg>Locally owned &amp; Operated</li>
  <li><svg width="20" height="20" viewBox="0 0 20 20" fill="none" stroke="#8cc63f" stroke-width="1.8"><circle cx="10" cy="10" r="8"/><path d="M6 10l3 3 5-6"/></svg>Professional Work</li>
  <li><svg width="20" height="20" viewBox="0 0 20 20" fill="none" stroke="#8cc63f" stroke-width="1.8"><circle cx="10" cy="10" r="8"/><path d="M6 10l3 3 5-6"/></svg>Safety is our no.1 priority</li>
  <li><svg width="20" height="20" viewBox="0 0 20 20" fill="none" stroke="#8cc63f" stroke-width="1.8"><circle cx="10" cy="10" r="8"/><path d="M6 10l3 3 5-6"/></svg>Free estimates</li>
  <li><svg width="20" height="20" viewBox="0 0 20 20" fill="none" stroke="#8cc63f" stroke-width="1.8"><circle cx="10" cy="10" r="8"/><path d="M6 10l3 3 5-6"/></svg>Licensed arborist on staff</li>
</ul>
<div class="abs btn" style="left:682px;top:2738px;width:132px;height:44px">Learn More</div>

<footer class="abs footer"></footer>
<svg class="abs" style="left:0;top:2860px" width="1200" height="140" viewBox="0 0 1200 140">
  <path d="M0 0 Q30 90 300 110 Q800 130 1200 40 L1200 0Z" fill="#fff"/>
  <path d="M0 0 Q30 90 300 110 Q800 130 1200 40" fill="none" stroke="#f7a234" stroke-width="6"/>
</svg>
<div class="abs" style="left:110px;top:3110px;display:flex;align-items:center;gap:12px"><span class="brand-dot"></span><span style="font-weight:700;font-size:24px;color:var(--white)">Verdell Tree Care</span></div>
<span class="abs social" style="left:111px"></span><span class="abs social" style="left:150px"></span><span class="abs social" style="left:189px"></span><span class="abs social" style="left:229px"></span>
<div class="abs f-head" style="left:404px;top:3098px">Quick Links</div>
<ul class="abs f-links" style="left:405px;top:3152px"><li>Home</li><li>Services</li><li>Blog</li><li>About</li><li>Contact</li></ul>
<div class="abs f-head" style="left:604px;top:3098px">Contact Us</div>
<div class="abs f-text" style="left:602px;top:3152px;font-size:13px;line-height:20px;width:220px">
  <div style="display:flex;gap:4px"><svg width="14" height="16" viewBox="0 0 14 16" fill="none" stroke="#fff" style="flex:none"><path d="M7 15s5-5 5-9A5 5 0 0 0 2 6c0 4 5 9 5 9z"/><circle cx="7" cy="6" r="2"/></svg><span>Lorem ipsum dolor sit amet, consectetur adipiscing</span></div>
  <div style="display:flex;gap:4px;margin-top:14px;align-items:center"><svg width="14" height="12" viewBox="0 0 14 12" fill="none" stroke="#fff"><rect x="1" y="1" width="12" height="10"/><path d="M1 1l6 5 6-5"/></svg>info@verdelltreecare.com</div>
  <div style="display:flex;gap:4px;margin-top:14px;align-items:center"><svg width="14" height="14" viewBox="0 0 24 24" fill="none" stroke="#fff" stroke-width="2"><path d="M5 3h4l2 5-3 2a12 12 0 0 0 6 6l2-3 5 2v4a2 2 0 0 1-2 2A17 17 0 0 1 3 5a2 2 0 0 1 2-2z"/></svg>(555) 014-7720</div>
</div>
<div class="abs f-head" style="left:880px;top:3098px">Quick Contact Form</div>
<div class="abs f-input" style="top:3155px;height:30px">Name*</div>
<div class="abs f-input" style="top:3193px;height:30px">Email*</div>
<div class="abs f-input" style="top:3231px;height:45px">Message*</div>
<div class="abs btn" style="left:878px;top:3288px;width:120px;height:40px;font-size:13px;font-weight:600">Submit Now ›</div>
<div class="abs" style="left:112px;top:3352px;width:976px;height:1px;background:#333"></div>
<div class="abs" style="left:0;top:3382px;width:1200px;text-align:center;font-size:13px;color:var(--white)">©Copyrights 2024 <span style="color:var(--green);text-decoration:underline">Verdell Tree Care</span> &nbsp;| &nbsp; All Rights Reserved</div>
</body>
</html>
```